Harborline Renewal Business Card Design

Professional and clean design. The design colors should flow with the logo. Two-sided card with the website on the back which is:

www.HarborlineRenewal.example.

"Specializing in Water Damage Restoration"

On the front I need the name, email, phone, and logo.

Name: Darnell Quisby
Email: Darnell@HarborlineRenewal.example
Phone: 555-318-2046 for now

I only have the Preview and Thumbnail right now but should have the source files uploaded within a day or two.

Target Market(s)

Flood victims, home owners with water damage from busted pipes etc...

Industry/Entity Type

Business

Contact Information for Business Card

Name: Darnell Quisby

Font styles to use
Serif
Sans Serif

Requirements
Must have
• Business Card Details Info

```html
<!DOCTYPE html>
<html lang="en">
<head>
<meta charset="utf-8">
<title>Harborline Renewal – Business Card</title>
<link rel="stylesheet" href="https://fonts.googleapis.com/css2?family=Open+Sans:wght@400;600;700&display=swap">
<style>
  :root {
    --page-bg: #eceff2;
    --blue-deep: #2a95d3;
    --blue-mid: #3ea9e2;
    --blue-light: #6cc6ef;
    --white: #ffffff;
    --name-tint: #d6ecf8;
    --card-shadow: rgba(20, 40, 60, 0.18);
  }
  * { box-sizing: border-box; margin: 0; padding: 0; }
  html, body {
    width: 1200px;
    height: 843px;
    overflow: hidden;
    background: var(--page-bg);
    font-family: "Open Sans", Arial, sans-serif;
  }
  .card-sheet {
    position: relative;
    width: 1200px;
    height: 843px;
  }
  .card {
    position: absolute;
    top: 267px;
    width: 540px;
    height: 309px;
    border-radius: 22px;
    overflow: hidden;
    box-shadow: 0 10px 30px var(--card-shadow);
  }
  .card svg.card-art { position: absolute; inset: 0; width: 100%; height: 100%; }
  .card--back {
    left: 40px;
    background: linear-gradient(135deg, #3aa6e0 0%, #2a92d0 100%);
  }
  .card--front { left: 620px; background: var(--white); }

  /* back side */
  .back-brand {
    position: absolute;
    left: 26px;
    bottom: 36px;
    color: var(--white);
  }
  .back-brand__name {
    font-weight: 600;
    font-size: 30px;
    letter-spacing: 1px;
    line-height: 1.1;
  }
  .back-brand__tagline {
    margin-top: 6px;
    font-size: 14px;
    font-weight: 600;
  }

  /* front side */
  .front-brand {
    position: absolute;
    top: 26px;
    left: 150px;
    width: 360px;
    text-align: center;
  }
  .front-brand__mark {
    display: block;
    width: 48px;
    height: 48px;
    margin: 0 auto 8px;
    border-radius: 50%;
    background: var(--blue-deep);
  }
  .front-brand__name {
    color: var(--blue-deep);
    font-weight: 600;
    font-size: 30px;
    letter-spacing: 1px;
    line-height: 1.1;
  }
  .contact-list {
    position: absolute;
    left: 22px;
    top: 184px;
    list-style: none;
    color: var(--white);
    font-size: 13px;
    line-height: 21px;
  }
  .contact-list__label { font-weight: 700; }
  .holder-name {
    position: absolute;
    right: 26px;
    bottom: 26px;
    color: var(--name-tint);
    font-weight: 700;
    font-size: 18px;
  }
</style>
</head>
<body>
<main class="card-sheet">

  <section class="card card--back" aria-label="Card back">
    <div class="back-brand">
      <p class="back-brand__name">HARBORLINE RENEWAL</p>
      <p class="back-brand__tagline">Specializing in Water Damage Restoration</p>
    </div>
  </section>

  <section class="card card--front" aria-label="Card front">
    <svg class="card-art" viewBox="0 0 540 309" aria-hidden="true">
      <defs>
        <linearGradient id="waveFill" x1="0" y1="0" x2="1" y2="0">
          <stop offset="0" stop-color="#6cc6ef"/>
          <stop offset="1" stop-color="#3ea9e2"/>
        </linearGradient>
      </defs>
      <rect width="540" height="309" fill="#ffffff"/>
      <path d="M0 166 C150 146 300 238 540 212 L540 309 L0 309 Z" fill="url(#waveFill)"/>
      <path d="M0 156 C150 136 300 228 540 202" fill="none" stroke="#2a95d3" stroke-width="3"/>
    </svg>
    <div class="front-brand">
      <span class="front-brand__mark"></span>
      <p class="front-brand__name">HARBORLINE RENEWAL</p>
    </div>
    <ul class="contact-list">
      <li><span class="contact-list__label">P:</span> 555-318-2046 for now</li>
      <li>Darnell@HarborlineRenewal.example</li>
      <li>www.HarborlineRenewal.example</li>
    </ul>
    <p class="holder-name">Darnell Quisby</p>
  </section>

</main>
</body>
</html>
```